develop our online residential property development appraisal service

This project requires a detailed WordPress design to represent a new digital residential property development consultancy business. At its heart it will have a number of different products that essentially advise customers of the potential value and feasibility of developing their residential site into multiple townhouses, units, apartments, etc... This will be accompanied by explaining the considerations of residential property development.

We aim to navigate and break down this complex area and provide our customers with the tools, knowledge, control and power to 'unlock the value' in their property.

REFERENCE DOCUMENTS:
1. Detailed solution requirements please refer to the attached 'wordpressdesignrequirements'
2. Logo files, style guide and colour pallet please refer to the attached 'KRLM.zip'
3. Site Map refer to attached 'wordpressdesignsitemap'

Reason: Additional information provided so extending period for designs to take into account.

Target Market(s)

The site will appeal to professional service providers; accountants, financial planners, lawyers, etc…

Industry/Entity Type

Residential

Font styles to use
Sans Serif
Other font styles liked:
• Similar to the logo font, slim line and simple

Requirements
Must have
• The logo, style and colour palette provided in the attached 'KRLM.zip' files
• Satisfy the intent of the 'wordpressdesignrequirements'
• Present as an online-centric business
• Clean, crisp and modern design
• Predominant use of white as a background contrasted with the colours provided in the colour palette
Nice to have
• Use of the following WordPress business themes is encouraged but not mandatory:
• 1. Mavo
• 2. Tulek
• 3. Vupa
Should not have
• Overt references to Australia

```html
<!DOCTYPE html>
<html lang="en">
<head>
<meta charset="utf-8">
<title>KRLM — Residential Development Appraisals</title>
<link href="https://fonts.googleapis.com/css2?family=Open+Sans:wght@300;400;600;700&display=swap" rel="stylesheet">
<style>
:root{
  --page-bg:#e4e3e4;
  --white:#ffffff;
  --bar-dark:#3d3b3c;
  --text:#444444;
  --text-soft:#8a8a8a;
  --heading:#222222;
  --rule:#d6d6d6;
  --footer-bg:#f0f0f0;
  --teal:#1fa89b;
  --green-mid:#3db56c;
  --green-light:#66c653;
  --button:#6ac56c;
  --link:#4cb94a;
  --line-blue:#1b9ad6;
  --line-green:#3fbd3f;
  --lawn:#7cc46a;
}
*{box-sizing:border-box;margin:0;padding:0}
html,body{width:1026px;height:1200px;overflow:hidden}
body{background:var(--page-bg);font-family:"Open Sans",Arial,sans-serif;color:var(--text);position:relative}
.site{position:absolute;left:180px;top:0;width:656px;height:1200px;background:var(--white)}
.topbar{height:17px;background:var(--bar-dark);color:#cfcfcf;font-size:8.5px;text-align:right;padding:3px 38px 0 0}
.masthead{position:relative;height:98px}
.brand{position:absolute;left:27px;top:38px;display:flex;align-items:center;gap:10px}
.brand-mark{width:14px;height:14px;background:var(--link)}
.brand-name{font-weight:600;font-size:30px;color:var(--heading);letter-spacing:1px;line-height:1}
.main-nav{position:absolute;right:30px;top:57px;font-size:10.5px;color:#333;display:flex;gap:6px}
.main-nav span.sep{color:#777}
.accent-line{height:5px;background:linear-gradient(90deg,var(--line-blue) 0%,#22a9b4 45%,var(--line-green) 100%)}
.hero{position:relative;height:342px;overflow:hidden}
.hero-illustration{position:absolute;inset:0;background:
  radial-gradient(ellipse 45% 42% at 52% 48%,#c9bfb4 0%,#e3ddd5 40%,transparent 70%),
  radial-gradient(ellipse 62% 60% at 45% 35%,var(--lawn) 0%,#b7dfa7 45%,#ffffff 85%)}
.hero-inset{position:absolute;left:474px;top:150px;width:112px;height:112px;border-radius:50%;border:3px solid var(--white);background:linear-gradient(180deg,#cfe2f2 0%,#d8d2c6 55%,#8a9a7a 100%)}
.hero-copy{position:absolute;left:58px;top:24px;width:94px;text-align:right;font-size:10px;font-weight:700;line-height:1.3;color:#3a4a38;hyphens:auto;-webkit-hyphens:auto}
.products{position:relative;height:304px;display:flex;padding:10px 0 0 30px}
.product{width:205px;display:flex;flex-direction:column;align-items:center}
.product-badges{position:relative;width:170px;height:120px}
.product-photo{position:absolute;left:8px;top:2px;width:112px;height:112px;border-radius:50%;background:linear-gradient(180deg,#bcd6ee 0%,#e4e2dc 50%,#7f8a74 100%)}
.product-label{position:absolute;left:64px;top:10px;width:100px;height:100px;border-radius:50%;color:var(--white);font-size:10.5px;text-align:center;display:flex;align-items:center;justify-content:center;line-height:1.3}
.product--a .product-label{background:var(--teal)}
.product--b .product-label{background:var(--green-mid)}
.product--c .product-label{background:var(--green-light)}
.product h3{margin-top:22px;font-size:9.5px;font-weight:700;color:var(--heading);letter-spacing:.3px}
.product p{margin-top:12px;width:167px;font-size:9.5px;line-height:1.4}
.btn{margin-top:12px;background:var(--button);color:var(--white);font-size:9.5px;font-weight:600;padding:7px 12px;border-bottom:2px solid #55ad57}
.widgets{position:absolute;top:766px;left:0;width:656px;height:206px;border-top:1px solid var(--rule);display:flex;padding:40px 0 0 38px;gap:38px}
.widget{width:167px;font-size:9.5px;line-height:1.4}
.widget h4{font-size:9.5px;font-weight:700;color:var(--heading);margin-bottom:16px}
.widget ul{list-style:none;margin-top:10px}
.widget ul.links li{color:var(--link);font-weight:600;padding-left:10px;position:relative}
.widget ul.links li::before{content:"";position:absolute;left:0;top:5px;width:4px;height:4px;border-radius:50%;background:var(--link)}
.news-item{padding-bottom:7px;margin-bottom:9px;border-bottom:1px solid #eee}
.news-item:last-child{border-bottom:none}
.news-item a{color:var(--link);font-weight:600;text-decoration:none;display:block}
.news-item time{font-size:8px;color:var(--text-soft)}
.footer-widgets{position:absolute;top:972px;left:0;width:656px;height:180px;background:var(--footer-bg);display:flex;padding:40px 0 0 38px;gap:38px}
.footer-widgets .widget h4{margin-bottom:12px}
.page-list{list-style:none}
.page-list li{font-size:8.5px;color:#aaa;height:18px;line-height:17px;border-bottom:1px solid #e2e2e2}
.page-list li:last-child{border-bottom:none}
.social{display:flex;gap:9px}
.social span{width:14px;height:14px;border-radius:50%;background:#9a9a9a}
.bottombar{position:absolute;top:1152px;left:0;width:656px;height:48px;background:var(--bar-dark);color:#e6e6e6;font-size:8px;padding:14px 38px 0 38px;display:flex;justify-content:space-between}
.bottombar .credits{line-height:1.6}
.footer-nav{font-weight:700;display:flex;gap:8px}
</style>
</head>
<body>
<div class="site">
  <div class="topbar">Phone: 1-202-555-0148</div>
  <header class="masthead">
    <div class="brand">
      <span class="brand-mark"></span>
      <span class="brand-name">KRLM</span>
    </div>
    <nav class="main-nav">
      <span>About Us</span><span class="sep">|</span><span>Social Media Integration</span><span class="sep">|</span><span>Contact Us</span>
    </nav>
  </header>
  <div class="accent-line"></div>

  <section class="hero">
    <div class="hero-illustration" role="img" aria-label="Cutaway 3D floor plan of a furnished apartment set on a green lawn"></div>
    <div class="hero-inset" role="img" aria-label="Photo of a modern townhouse development"></div>
    <p class="hero-copy">Proin cursus quis massa id sollicitudin. Mauris et nulla eget dolor dictum posuere eget et lacus. Aenean convallis felis sed ultricies semper. Integer finibus egestas nisi, a tempus elit lacinia eget. Morbi tristique lacinia sagittis. Nullam ut enim in odio aliquam ultrices</p>
  </section>

  <section class="products">
    <article class="product product--a">
      <div class="product-badges">
        <div class="product-photo" role="img" aria-label="Photo of a residential apartment building"></div>
        <div class="product-label">Property<br>Report<br>Page A</div>
      </div>
      <h3>GRID PAGE</h3>
      <p>The Grid Page Template displays all child pages of the page in a grid format. You might use this for your case studies or services page, for example.</p>
      <span class="btn">READ MORE</span>
    </article>
    <article class="product product--b">
      <div class="product-badges">
        <div class="product-photo" role="img" aria-label="Photo of a modern multi-level residence"></div>
        <div class="product-label">Property<br>Report<br>Page B</div>
      </div>
      <h3>FULL WIDTH PAGE</h3>
      <p>The Full Width Page Template is fitting for embedding a map, a video, or a contact form.</p>
      <span class="btn">READ MORE</span>
    </article>
    <article class="product product--c">
      <div class="product-badges">
        <div class="product-photo" role="img" aria-label="Photo of contemporary townhouses"></div>
        <div class="product-label">Property<br>Report<br>Page C</div>
      </div>
      <h3>ALTERNATE SIDEBAR PAGE</h3>
      <p>The Alternate Sidebar Page template will overrule the default sidebar position on a given page, and that page's sidebar will appear on the opposite side.</p>
      <span class="btn">READ MORE</span>
    </article>
  </section>

  <section class="widgets">
    <div class="widget">
      <h4>FRONT PAGE WIDGETS</h4>
      <p>This area of your home page is configured by going to Dashboard → Appearance → Widgets and adding widgets in the Front Page widget areas.</p>
    </div>
    <div class="widget">
      <h4>CUSTOM PAGE TEMPLATES</h4>
      <p>Tulek has four custom page templates that are great for business and corporate websites:</p>
      <ul class="links">
        <li>Front Page Template</li>
        <li>Full Width Page Template</li>
        <li>Grid Page Template</li>
        <li>Alternate Sidebar Page Template</li>
      </ul>
    </div>
    <div class="widget">
      <h4>RECENT NEWS</h4>
      <div class="news-item"><a>New identity</a><time>July 30, 2014</time></div>
      <div class="news-item"><a>Tulek is taking the day off</a><time>July 22, 2014</time></div>
      <div class="news-item"><a>A Short Post</a><time>July 21, 2014</time></div>
    </div>
  </section>

  <section class="footer-widgets">
    <div class="widget">
      <h4>PAGES</h4>
      <ul class="page-list">
        <li>HOME</li>
        <li>About Us</li>
        <li>Who Are We ?</li>
        <li>What Do We Do ?</li>
        <li>How Do We Do It ?</li>
        <li>Site Map</li>
      </ul>
    </div>
    <div class="widget">
      <h4>RESPONSIVE DESIGN</h4>
      <p>Tulek's layout adjusts itself depending on the device you are using. This means your site will look good not only on laptop browsers, but also on devices with smaller screens, such as a tablet and a phone.</p>
    </div>
    <div class="widget">
      <h4>FOLLOW US</h4>
      <div class="social" aria-label="Social profiles"><span></span><span></span><span></span><span></span><span></span></div>
    </div>
  </section>

  <footer class="bottombar">
    <div class="credits">Create a free website or blog at SitePress.com. | The Tulek Theme by<br>SitePress.com.</div>
    <nav class="footer-nav"><span>BLOG</span><span>ABOUT US</span><span>CONTACT US</span></nav>
  </footer>
</div>
</body>
</html>
```